Zing Webcomic

A simple signup landing page and blog design for an upcoming webcomic. I am mostly looking for a flat UI with a simple color scheme. I want to showcase a large background image and the comic title image. I have all the technicals figured out (I am a web developer by trade), so all I need now is a solid design I like.

The signup for should only have one field (email) and have text above it, and smaller text below it.

The blog, I am thinking, should be in the style of comic book pages. The home page would be blocks with large white outlines, with the article pages being an extension of that. As I stated before, should be fairly minimalist, but fun. Also, no sidebar or ads, IE single column. I have attached a simple mockup/layout of the blog to give a general idea of what I am going for.

I have attached the Logo and Background art (uncolored) for reference. Don't worry about the background image blending in, I can take care of that when the design is implemented. I will be focusing on layout and overall look, not necessarily readability (which I can fix).

~Please DO NOT take these examples literally. I will describe what I like about each example.~

Signup pages:
http://example-plaza.test/landing-page-type-photo/
http://www.lanternhop.test/showcase/website-design/814/10-most-beautiful-landing-pages-in-minimalist-style
http://quillnest.test/47-modern-landing-pages-showcasing-inspirational-web-design/
Great examples of minimalist design. However, instead of text or other content, there should be a simple signup form, as described above. Also think a lot more "playful" rather than super professional.

Blog:
http://vrakk.test/
Awesome example of a single column, minimal design. Needs to be more "comicbook style" though.
http://tidyrows.test/
Another good example of minimal design blog.
http://makerbarn.test/wp-content/uploads/res-blogs-5.jpg
I like the timeline feel here. Combine that with a comic book page kind of thing, and I think you have a winner.

Actual webcomic landing (not required):
http://www.lunarfoxpanels.test/comic.php?date=20021104#.U90ysYBdUvU
I like the navigation. It makes the atmosphere nice for the comic. The page layout itself is WAY too busy.
http://www.dime-galaxy.test/comic/
Fairly common webcomic, but their navigation and page layout is nice.
http://qvmp.test/936/
Another common webcomic. The simple page layout makes it easy for people to get started I think.

So there you have it. I will try my best to keep updating and adding to the description. If you have any questions, please don't hesitate to ask.
Updates

Hey Guys, I am really appreciating all the effort you have been putting in. I am amazed to see all the awesome designs and all the care taken with the project. I am just writing everyone to let you know that I have uploaded a simple layout/wireframe of the blog, to give an idea of what I am going for. Can't wait to see how things progress, and good luck to everyone!

Industry/Entity Type

Trade

Font styles to use
Sans Serif

Requirements
Must have
• Must showcase a large background image (does not have to cover the entire background). Should be a flat UI as well. Should be mostly neutral with splashes of blue or purple. Social links should also be somewhere (twitter, facebook, etc.).
Nice to have
• I am thinking something with rounded boxes, but I can live without them. A more "fun" design as opposed to more professional is definitely nice to have.

If you would like to try a stab at the actual comic page display and navigation, you are welcome to submit something. It should not be a main priority though.

Being responsive is not a requirement, but it would be nice to have.
Should not have
• A billion links in the navigation or look too busy.
No sidebar or advertisements. Should be a clean design.

```html
<!DOCTYPE html>
<html lang="en">
<head>
<meta charset="utf-8">
<title>Zing Webcomic — Coming Soon</title>
<link rel="stylesheet" href="https://fonts.googleapis.com/css2?family=Raleway:wght@400;500;700;800&display=swap">
<style>
  :root {
    --blue-deep: #0a4a9c;
    --blue-mid: #0f63b8;
    --blue-glow: #1794da;
    --blue-edge: #083f86;
    --button-blue: #0f8ff0;
    --white: #ffffff;
    --placeholder: #8a8f96;
    --icon-fill: #d6dde6;
    --icon-active: #2c2f35;
  }
  * { box-sizing: border-box; margin: 0; padding: 0; }
  html, body {
    width: 1200px;
    height: 676px;
    overflow: hidden;
  }
  body {
    font-family: "Raleway", sans-serif;
    color: var(--white);
    position: relative;
  }
  .hero-art {
    position: absolute;
    inset: 0;
    background:
      radial-gradient(ellipse 520px 300px at 600px 60px, rgba(40,170,235,0.55), rgba(40,170,235,0) 70%),
      radial-gradient(ellipse 900px 600px at 600px 200px, var(--blue-mid), var(--blue-deep) 75%, var(--blue-edge));
  }
  .page {
    position: relative;
    width: 1200px;
    height: 676px;
  }
  .brand {
    position: absolute;
    top: 22px;
    left: 0;
    right: 0;
    text-align: center;
    font-weight: 800;
    font-size: 54px;
    letter-spacing: 4px;
    text-transform: uppercase;
    color: var(--white);
  }
  .tagline {
    position: absolute;
    top: 268px;
    left: 0;
    right: 0;
    text-align: center;
    font-weight: 500;
    font-size: 26px;
    line-height: 40px;
  }
  .signup {
    position: absolute;
    top: 385px;
    left: 364px;
    width: 450px;
    height: 49px;
    display: flex;
  }
  .signup-email {
    flex: 0 0 320px;
    border: none;
    border-radius: 3px 0 0 3px;
    background: var(--white);
    padding: 0 14px;
    font-family: "Raleway", sans-serif;
    font-size: 12px;
    color: #333;
    outline: none;
  }
  .signup-email::placeholder { color: var(--placeholder); }
  .signup-send {
    flex: 1;
    border: none;
    border-radius: 0 3px 3px 0;
    background: var(--button-blue);
    color: var(--white);
    font-family: "Raleway", sans-serif;
    font-weight: 700;
    font-size: 14px;
    letter-spacing: 0.5px;
    text-transform: uppercase;
    cursor: pointer;
  }
  .social {
    position: absolute;
    top: 617px;
    left: 0;
    right: 0;
    display: flex;
    justify-content: center;
    gap: 8px;
    list-style: none;
  }
  .social-link {
    display: block;
    width: 25px;
    height: 25px;
    border-radius: 50%;
    background: var(--icon-fill);
  }
  .social-link.is-active { background: var(--icon-active); box-shadow: 0 0 0 2px var(--icon-fill) inset; }
  .visually-hidden {
    position: absolute;
    width: 1px; height: 1px;
    overflow: hidden;
    clip: rect(0 0 0 0);
    white-space: nowrap;
  }
  .copyright {
    position: absolute;
    top: 656px;
    left: 0;
    right: 0;
    text-align: center;
    font-size: 10px;
    font-weight: 500;
  }
</style>
</head>
<body>
  <div class="hero-art" role="img" aria-label="Large faint blue line-art background of comic characters in front of city buildings"></div>
  <main class="page">
    <h1 class="brand">Zing</h1>
    <p class="tagline">Lorem ipsum dolor sit amet, consectetur adipisicing elit,<br>sed do eiusmod tempor incididunt ut labore</p>
    <form class="signup" action="#">
      <input class="signup-email" type="email" placeholder="Enter your email" aria-label="Email address">
      <button class="signup-send" type="submit">Send</button>
    </form>
    <ul class="social">
      <li><a class="social-link" href="#"><span class="visually-hidden">Microblog</span></a></li>
      <li><a class="social-link" href="#"><span class="visually-hidden">Social network</span></a></li>
      <li><a class="social-link is-active" href="#"><span class="visually-hidden">Pinboard</span></a></li>
      <li><a class="social-link" href="#"><span class="visually-hidden">Community</span></a></li>
      <li><a class="social-link" href="#"><span class="visually-hidden">Professional network</span></a></li>
      <li><a class="social-link" href="#"><span class="visually-hidden">Video channel</span></a></li>
    </ul>
    <p class="copyright">Copyright © 2014 Zing Webcomic All rights reserved.</p>
  </main>
</body>
</html>
```